Allied Health team of Physiotherapists & Occupational Therapists seek a business card design

We have our new logo, we now need our new business cards and stationary. Tidewell: Oedema & Family Clinic is seeking a generic card design to represent our whole team and individual cards for each therapist that incorporates our new logo to communicate our holistic approach that is calming, nuturing, supportive and welcoming.
Our Physiotherapists and Occupational Therapists assess, treat and provide education for people who are at risk of or who have lymphoedema. This is often as a result of treatment for cancer. We provide pre-operative and post-operative management and cancer rehabilitation in our Pilates studio. Our team also consists of Physiotherapists who have a strong interest in pelvic floor and continence management for both men and women.

Target Market(s)

Mainly women health conscious

Industry/Entity Type

Allied Health: Physiotherapy / Occupational Therapy

Contact Information for Business Card

Address: 14 Gallivant Ave Frankston 3199 Phone: 84316570 fax: 8431 6578 Email: info@tidewellcareservices.com.au Website: tidewellcareservices.com.au Facebook address: facebook.com/TidewellOedemaAndFamilyCareClinic. Room to write appointments. Individual cards need to have name, office email and individual email and professional details

Requirements
Must have
• Logo as per uploaded documents

```html
<!DOCTYPE html>
<html lang="en">
<head>
<meta charset="utf-8">
<title>Tidewell: Oedema &amp; Family Clinic — Business Card</title>
<link href="https://fonts.googleapis.com/css2?family=Marcellus&family=Arimo:wght@400&family=Open+Sans:wght@800&display=swap" rel="stylesheet">
<style>
  :root {
    --backdrop: #e9e6e2;
    --peach: #f7ae80;
    --charcoal: #2c2c2e;
    --cream: #fdf8e1;
    --ink: #111111;
    --white: #ffffff;
  }
  * { box-sizing: border-box; margin: 0; padding: 0; }
  html, body {
    width: 1200px; height: 900px; overflow: hidden;
    background: var(--backdrop);
  }
  .canvas {
    position: relative; width: 1200px; height: 900px;
  }
  .card {
    position: absolute; left: 290px; width: 620px; height: 354px;
    overflow: hidden;
    box-shadow: 0 6px 18px rgba(0,0,0,.18);
  }
  .card--front { top: 70px; background: var(--peach); }
  .card--back { top: 476px; background: var(--charcoal); }

  .brand {
    font-family: "Marcellus", serif;
    text-align: center;
    line-height: 1.15;
    display: flex; align-items: center; gap: 12px;
  }
  .brand__dot { width: 14px; height: 14px; border-radius: 50%; flex: none; }
  .brand__name { display: block; }
  .brand__sub { display: block; font-size: .5em; letter-spacing: .12em; text-transform: uppercase; }

  .card--front .brand {
    position: absolute; left: 50%; top: 50%; transform: translate(-50%, -50%);
    color: var(--ink); font-size: 46px;
  }
  .card--front .brand__dot { background: var(--ink); }

  .card--back .brand {
    position: absolute; right: 30px; top: 108px;
    color: var(--peach); font-size: 28px; flex-direction: column; gap: 6px;
  }
  .card--back .brand__dot { background: var(--peach); width: 10px; height: 10px; }

  .wave { position: absolute; inset: 0; width: 620px; height: 354px; }

  .profile { position: absolute; left: 40px; top: 28px; color: var(--white); }
  .profile__name {
    font-family: "Marcellus", serif; color: var(--peach);
    font-size: 25px; letter-spacing: .08em; font-weight: 400;
    margin-bottom: 8px;
  }
  .profile__quals { font-family: "Arimo", sans-serif; font-size: 13px; line-height: 17px; list-style: none; }
  .profile__roles {
    font-family: "Open Sans", sans-serif; font-weight: 800;
    font-size: 14px; line-height: 17px; list-style: none; margin-top: 12px;
  }
  .contact {
    list-style: none; margin-top: 12px;
    font-family: "Arimo", sans-serif; font-size: 13.5px; line-height: 20px;
  }
  .contact__item { display: flex; align-items: center; gap: 9px; }
  .contact__icon { width: 14px; height: 14px; flex: none; }
</style>
</head>
<body>
<main class="canvas">

  <section class="card card--front" aria-label="Card front">
    <div class="brand">
      <span class="brand__dot"></span>
      <span>
        <span class="brand__name">Tidewell</span>
        <span class="brand__sub">Oedema &amp; Family Clinic</span>
      </span>
    </div>
  </section>

  <section class="card card--back" aria-label="Card back">
    <svg class="wave" viewBox="0 0 620 354" aria-hidden="true">
      <path d="M0,320 C150,352 300,310 430,245 C510,205 570,184 620,170 L620,354 L0,354 Z" fill="var(--peach)"/>
      <path d="M0,300 C140,335 280,300 410,236 C300,300 150,330 0,320 Z" fill="var(--cream)"/>
    </svg>

    <div class="brand">
      <span class="brand__dot"></span>
      <span>
        <span class="brand__name">Tidewell</span>
        <span class="brand__sub">Oedema &amp; Family Clinic</span>
      </span>
    </div>

    <div class="profile">
      <h1 class="profile__name">MAREN HOLT</h1>
      <ul class="profile__quals">
        <li>B. Physio (Hons), B.App.Sci.(Human Movement/Psych)</li>
        <li>Post Grad Certif. Exercise for Women</li>
        <li>Post Grad Certif. Continence &amp; Pelvic Floor Rehabilitation</li>
      </ul>
      <ul class="profile__roles">
        <li>Physiotherapist</li>
        <li>Lymphoedema &amp; Oncology Rehabilitation</li>
        <li>Continence &amp; Pelvic Floor</li>
      </ul>
      <ul class="contact">
        <li class="contact__item">
          <svg class="contact__icon" viewBox="0 0 24 24"><path fill="var(--peach)" d="M6.6 10.8a15.1 15.1 0 0 0 6.6 6.6l2.2-2.2c.3-.3.7-.4 1-.2 1.1.4 2.3.6 3.6.6.6 0 1 .4 1 1V20c0 .6-.4 1-1 1A17 17 0 0 1 3 4c0-.6.4-1 1-1h3.5c.6 0 1 .4 1 1 0 1.3.2 2.5.6 3.6.1.3 0 .7-.2 1z"/></svg>
          <span>000 1111 2222</span>
        </li>
        <li class="contact__item">
          <svg class="contact__icon" viewBox="0 0 24 24"><rect x="2" y="5" width="20" height="14" fill="var(--peach)"/><path d="M2 5l10 8 10-8" fill="none" stroke="var(--charcoal)" stroke-width="1.6"/></svg>
          <span>info@tidewellcareservices.com.au</span>
        </li>
        <li class="contact__item">
          <svg class="contact__icon" viewBox="0 0 24 24"><rect x="2" y="5" width="20" height="14" fill="var(--peach)"/><path d="M2 5l10 8 10-8" fill="none" stroke="var(--charcoal)" stroke-width="1.6"/></svg>
          <span>name@tidewellcareservices.com.au</span>
        </li>
        <li class="contact__item">
          <svg class="contact__icon" viewBox="0 0 24 24" fill="none" stroke="var(--peach)" stroke-width="2"><circle cx="12" cy="12" r="9.5"/><ellipse cx="12" cy="12" rx="4" ry="9.5"/><path d="M2.5 12h19M4.5 7h15M4.5 17h15"/></svg>
          <span>www.tidewellcareservices.com.au</span>
        </li>
      </ul>
    </div>
  </section>

</main>
</body>
</html>
```